Tellmora Corporate Stationery

Look for design of all new corporate stationery for an existing insurance broking business that is going through a redesign and move from older partners to younger family members. New Logo is attached. Company is Brisbane based.
Colours in the Logo is Hex #43bed8 and website features a lot of hex #17b8d8. Website front page "A plan to protect you" - headline. "Professional and Individual advice to protect your greatest assets" - tagline.

Stationery required: Business Cards, Letter head, Thank-you cards, Birthday cards, Presentation folders, With Compliment slips and a powerpoint template. We also would like to send a card to all customers with the something along of the lines of "something new".

Target Market(s)

Customers of Insurance business looking at superannuation, life and income protection insurance, investment advice and wills

Industry/Entity Type

Insurance Broker

Font styles to use
Other font styles liked:
• same as logo

Requirements
Must have
• The above designs for new stationery for the new business including:
• Business Cards, Letter head, Thank-you cards, Birthday cards, Presentation folders, With Compliment slips and a powerpoint template. We also would like to send a card to all customers with the something along of the lines of "something new".
Nice to have
• It is a new look - long time family business being passed to next generation - big focus on advice for YOU, individual advice etc..

```html
<!DOCTYPE html>
<html lang="en">
<head>
<meta charset="utf-8">
<title>Tellmora Business Card</title>
<link href="https://fonts.googleapis.com/css2?family=Ubuntu:ital,wght@0,300;0,400;0,500;1,400&display=swap" rel="stylesheet">
<style>
  :root {
    --cyan: #43bed8;
    --grey: #808285;
    --ring: #e6e7e8;
    --paper: #ffffff;
    --page: #ffffff;
  }
  * { box-sizing: border-box; margin: 0; padding: 0; }
  html, body {
    width: 1200px; height: 1000px; overflow: hidden;
    background: var(--page);
    font-family: "Ubuntu", sans-serif;
  }
  .canvas { position: relative; width: 1200px; height: 1000px; }
  .card {
    position: absolute; left: 207px; width: 786px; overflow: hidden;
    background: var(--paper);
    box-shadow: 0 0 8px rgba(0,0,0,0.18);
  }
  .card--front { top: 0; height: 487px; }
  .card--back { top: 515px; height: 485px; }
  .ring-pattern {
    position: absolute; inset: 0;
    background: radial-gradient(circle at 50% 45%, #f3f3f4 0%, #ebebec 60%, #e4e4e5 100%);
  }
  .card--back .ring-pattern {
    background: radial-gradient(circle at 80% 55%, #f3f3f4 0%, #ebebec 55%, #e2e2e3 100%);
  }
  .brand-plate {
    position: absolute; left: 130px; top: 96px; width: 526px; height: 306px;
    background: var(--paper); border-radius: 40px;
    display: flex; flex-direction: column; align-items: center; justify-content: center;
  }
  .brand-dot {
    width: 150px; height: 150px; border-radius: 50%;
    background: var(--cyan); margin-bottom: 22px;
  }
  .brand-name {
    color: var(--cyan); font-weight: 500; font-size: 72px; line-height: 1;
    letter-spacing: 2px; text-transform: uppercase;
  }
  .brand-sub {
    color: var(--cyan); font-weight: 500; font-size: 34px; line-height: 1.2;
    letter-spacing: 2px; text-transform: uppercase; margin-top: 6px;
  }
  .focus-disc {
    position: absolute; left: 185px; top: -200px; width: 880px; height: 880px;
    border-radius: 50%; background: var(--paper);
  }
  .tagline {
    position: absolute; left: 480px; top: 38px; width: 290px;
    text-align: center; color: var(--grey); font-style: italic;
    font-size: 18px; line-height: 29.5px;
  }
  .contact-list { position: absolute; left: 44px; top: 145px; list-style: none; }
  .contact-item {
    position: relative; width: 459px; height: 34px; margin-bottom: 19px;
    background: var(--cyan); border-radius: 17px;
    color: #fff; font-size: 21px; line-height: 34px; padding-left: 79px;
  }
  .contact-icon {
    position: absolute; left: 20px; top: -5px; width: 44px; height: 44px;
  }
  .advisor-mark {
    position: absolute; left: 528px; top: 145px; width: 194px; height: 194px;
    border-radius: 50%; border: 8px solid var(--cyan);
    display: flex; align-items: center; justify-content: center;
    color: var(--cyan); font-size: 36px; font-weight: 500;
  }
  .advisor { position: absolute; left: 528px; top: 366px; width: 194px; text-align: center; color: var(--grey); }
  .advisor-name { font-weight: 300; font-size: 44px; line-height: 1; }
  .advisor-role { font-weight: 400; font-size: 20px; margin-top: 2px; }
</style>
</head>
<body>
<div class="canvas">
  <section class="card card--front">
    <div class="ring-pattern" role="img" aria-label="Soft grey concentric ring background pattern"></div>
    <div class="brand-plate">
      <div class="brand-dot"></div>
      <div class="brand-name">Tellmora</div>
      <div class="brand-sub">Financial Group</div>
    </div>
  </section>

  <section class="card card--back">
    <div class="ring-pattern" role="img" aria-label="Soft grey concentric ring background pattern"></div>
    <div class="focus-disc"></div>
    <p class="tagline">“Professional and individual advice to protect your greatest assets”</p>
    <ul class="contact-list">
      <li class="contact-item">
        <svg class="contact-icon" viewBox="0 0 44 44"><circle cx="22" cy="22" r="21" fill="#fff"/><circle cx="22" cy="22" r="18" fill="var(--cyan)"/><path d="M9 23 L22 11 L35 23 M13 21 V33 H31 V21" fill="none" stroke="#fff" stroke-width="3" stroke-linejoin="round"/><rect x="19" y="25" width="6" height="8" fill="#fff"/></svg>
        48 Harbour Vale St. Brisbane
      </li>
      <li class="contact-item">
        <svg class="contact-icon" viewBox="0 0 44 44"><circle cx="22" cy="22" r="21" fill="#fff"/><circle cx="22" cy="22" r="18" fill="var(--cyan)"/><path d="M18 8 H24 V16 H21 V28 H24 V36 H18 Q14 36 14 30 V14 Q14 8 18 8 Z" fill="#fff"/></svg>
        (07) 5550 2718
      </li>
      <li class="contact-item">
        <svg class="contact-icon" viewBox="0 0 44 44"><circle cx="22" cy="22" r="21" fill="#fff"/><circle cx="22" cy="22" r="18" fill="var(--cyan)"/><rect x="8" y="13" width="28" height="18" fill="#fff"/><path d="M8 13 L22 24 L36 13" fill="none" stroke="var(--cyan)" stroke-width="2"/></svg>
        contact@tellmorafinance.com
      </li>
      <li class="contact-item">
        <svg class="contact-icon" viewBox="0 0 44 44"><circle cx="22" cy="22" r="21" fill="#fff"/><circle cx="22" cy="22" r="18" fill="var(--cyan)"/><circle cx="22" cy="22" r="12" fill="#fff"/><path d="M10 22 H34 M22 10 V34 M22 10 Q14 22 22 34 M22 10 Q30 22 22 34" fill="none" stroke="var(--cyan)" stroke-width="1.5"/></svg>
        www.tellmorafinance.com
      </li>
    </ul>
    <div class="advisor-mark">Tellmora</div>
    <div class="advisor">
      <div class="advisor-name">Alex Marlow</div>
      <div class="advisor-role">Financial Advisor</div>
    </div>
  </section>
</div>
</body>
</html>
```